New AI Company Needs a Powerpoint

We are a new type of AI company called KestrovaAI. Our AI uses human inspired approaches and put the human on the center of all our solutions. We need a standard company powerpoint design to use with potential investors, customers and partners to introduce our company and explain how the approach we take to AI is very different than others.
We want a design that is clean, modern, and playful. We do not want it to look overly robotic or cliche techy. Our mission is to remind the world that technology is a tool to be used to enhance and assist not to replace real humans.
We want a design that can show boring things (like financial info) in engaging ways.

Please use colors in logo variations along with a vibrant complementary color palette of your choosing,

Industry/Entity Type

Technology

Font styles to use
Sans Serif
Other font styles liked:
• Opensans

Colors
0054AA
0677BA
7BADD7
CADEEF
E8F1F8
0094D4
00A9DD
6FCCEA
C7EBF8
E9F6FB
00AB8E
00BBA5
67D7C9
C6EFE9
E9F9F6
59FF00
82FF00
B8FF75
E3FFCB
F4FFEA

Requirements
Must have
• Must incorporate logo colors and style

```html
<!DOCTYPE html>
<html lang="en">
<head>
<meta charset="utf-8">
<title>KestrovaAI — Company Presentation</title>
<link href="https://fonts.googleapis.com/css2?family=Montserrat:wght@400;600;700;800&family=Open+Sans:wght@400;600&display=swap" rel="stylesheet">
<style>
:root{
  --canvas:#6e6e6e;
  --white:#ffffff;
  --navy:#1a1c45;
  --navy-deep:#1c1f5e;
  --ink:#1e1e2a;
  --body:#555a66;
  --blue:#0094d4;
  --blue-mid:#1f95c8;
  --footer:#e2e2e2;
  --teal:#1f7f8c;
  --crimson:#a8183a;
  --olive:#9a9a1c;
  --amber:#e0961f;
  --indigo:#15157c;
}
*{margin:0;padding:0;box-sizing:border-box}
html,body{width:1200px;height:4129px;overflow:hidden;background:var(--canvas)}
body{position:relative;font-family:"Open Sans",Arial,sans-serif;color:var(--body)}
.slide{position:absolute;left:51px;width:1096px;height:616px;background:var(--white);overflow:hidden}
.abs{position:absolute}
.brand{font-family:"Montserrat",Arial,sans-serif;font-weight:800;color:var(--navy);letter-spacing:.5px;text-transform:uppercase}
.slide-title{position:absolute;left:90px;top:20px;font-family:"Montserrat",Arial,sans-serif;font-weight:700;font-size:18px;color:var(--ink)}
.header-brand{position:absolute;right:92px;top:24px;font-size:13px}
.header-rule{position:absolute;left:90px;top:66px;width:914px;height:2px;background:var(--ink)}
.header-accent{position:absolute;left:405px;top:73px;width:286px;height:3px;background:var(--blue-mid)}
.footer{position:absolute;left:0;bottom:0;width:100%;height:45px;background:var(--footer)}
.social{position:absolute;left:49px;top:12px;display:flex;gap:6px}
.social span{width:22px;height:22px;border:1.5px solid var(--ink);border-radius:50%}
.page-no{position:absolute;width:30px;height:30px;border-radius:50%;background:var(--ink);color:var(--white);font:700 10px/30px "Montserrat",sans-serif;text-align:center}
.footer .page-no{right:45px;top:8px}
.lorem{font-size:11px;line-height:23px;text-align:justify}
.photo{position:absolute}
/* slide 1 */
.welcome{left:48px;top:199px;font:700 14px "Montserrat",sans-serif;color:var(--blue-mid)}
.hero-title{left:48px;top:226px;font-size:38px}
.intro{left:48px;top:290px;width:560px}
.intro p+p{margin-top:23px}
/* slide 2 */
.point h3{font:700 14px "Montserrat",sans-serif;color:var(--ink);margin-bottom:14px}
.point p{font-size:10.5px;line-height:17px;color:var(--body)}
.point.left{text-align:right}
.point.bottom h3{margin:14px 0 0}
/* slide 3 */
.feature-head{left:383px;top:107px;width:335px;height:51px;background:var(--navy);color:var(--white);font:600 17px/51px "Montserrat",sans-serif;text-align:center;letter-spacing:.5px}
.feature-body{left:383px;top:158px;width:335px;height:356px;background:var(--blue-mid);color:var(--white);padding:12px 18px;font-size:10.4px;line-height:17px;text-align:justify}
.feature-body p+p{margin-top:17px}
/* slide 4 */
.chart-intro{left:88px;top:94px;width:920px;font-size:8.5px;line-height:17px;color:var(--body)}
.baseline{left:48px;top:420px;width:1000px;height:1px;background:#dcdcdc}
.bar-label{position:absolute;width:160px;text-align:center}
.bar-label i{display:block;margin:0 auto;width:22px;height:22px;border-radius:50%;background:var(--navy);border:4px solid var(--blue-mid)}
.bar-label h4{margin-top:8px;font:700 11.5px "Montserrat",sans-serif;color:var(--ink)}
.bar-label p{font-size:9.5px;line-height:14px;margin-top:5px}
/* slide 5 */
.story{left:48px;top:94px;width:630px;font-size:10.2px;line-height:17px;color:var(--ink);text-align:justify}
.framed{border:6px solid var(--white)}
/* slide 6 */
.closing{background:var(--navy-deep)}
.closing-brand{left:0;width:100%;top:143px;text-align:center;color:var(--white);font-size:36px;letter-spacing:2px}
.thanks{left:0;width:100%;top:266px;text-align:center;color:var(--white);font:800 38px "Montserrat",sans-serif;letter-spacing:1px}
.contact{position:absolute;top:358px;width:240px;text-align:center;color:var(--white)}
.contact .icon{width:56px;height:56px;border-radius:50%;background:var(--blue-mid);margin:0 auto;display:flex;align-items:center;justify-content:center}
.contact h5{margin-top:20px;font:700 13px "Montserrat",sans-serif;letter-spacing:.5px}
.contact p{margin-top:12px;font-size:13px;line-height:22px}
</style>
</head>
<body>

<!-- Slide 1: Welcome -->
<section class="slide" style="top:51px">
  <div class="abs brand" style="left:53px;top:48px;font-size:26px">KestrovaAI</div>
  <svg class="abs" style="left:600px;top:0" width="496" height="520" viewBox="600 0 496 520">
    <circle cx="910" cy="221" r="262" fill="none" stroke="var(--blue-mid)" stroke-width="12"/>
    <circle cx="910" cy="221" r="240" fill="var(--navy)"/>
    <circle cx="910" cy="221" r="214" fill="none" stroke="var(--blue-mid)" stroke-width="8"/>
    <defs><linearGradient id="office" x1="0" y1="0" x2="1" y2="1"><stop offset="0" stop-color="#e9ecef"/><stop offset=".55" stop-color="#9aa4ad"/><stop offset="1" stop-color="#3b3f48"/></linearGradient></defs>
    <circle cx="910" cy="221" r="205" fill="url(#office)" role="img" aria-label="Photo of a team meeting around a conference table"/>
  </svg>
  <div class="abs welcome">Welcome to</div>
  <div class="abs brand hero-title">KestrovaAI</div>
  <div class="abs lorem intro">
    <p>Lorem ipsum dolor sit amet, consectetur adipiscing elit, sed do eiusmod tempor incididunt ut labore et dolore magna aliqua. Ut enim ad minim veniam, quis nostrud exercitation ullamco laboris nisi ut aliquip ex ea commodo consequat. Duis aute irure dolor in reprehenderit in voluptate velit esse cillum dolore eu fugiat nulla pariatur. Excepteur sint occaecat cupidatat non proident, sunt in culpa qui officia deserunt mollit anim id est laborum. Lorem ipsum dolor sit amet, consectetur adipiscing elit, sed do eiusmod tempor incididunt ut labore et dolore magna aliqua. Ut enim ad minim veniam, quis nostrud exercitation ullamco laboris nisi ut aliquip ex ea commodo consequat. Duis aute irure dolor in reprehenderit in voluptate velit esse cillum dolore eu fugiat nulla pariatur. Excepteur sint occaecat cupidatat non proident.</p>
    <p>Lorem ipsum dolor sit amet, consectetur adipiscing elit, sed do eiusmod tempor incididunt ut labore et dolore magna aliqua. Ut enim ad minim veniam, quis nostrud exercitation ullamco laboris nisi ut aliquip ex ea commodo consequat. Duis aute irure dolor in reprehenderit in voluptate</p>
  </div>
  <div class="page-no" style="left:1022px;top:566px">1</div>
</section>

<!-- Slide 2: Four pillars -->
<section class="slide" style="top:731px">
  <h2 class="slide-title">Nemo enim ipsam voluptatem quia voluptas sit</h2>
  <div class="brand header-brand">KestrovaAI</div>
  <div class="header-rule"></div><div class="header-accent"></div>

  <svg class="abs" style="left:0;top:0" width="1096" height="570" viewBox="0 0 1096 570" fill="none">
    <g stroke="#8a8f99" stroke-width="1">
      <path d="M140 250H418L495 266"/><path d="M955 250H682L603 266"/>
      <path d="M140 463H418L495 370"/><path d="M955 463H682L603 370"/>
    </g>
    <g fill="var(--blue-mid)"><circle cx="495" cy="266" r="3"/><circle cx="603" cy="266" r="3"/><circle cx="495" cy="370" r="3"/><circle cx="603" cy="370" r="3"/></g>
    <g fill="var(--navy)">
      <path d="M549 107L608 162A60 60 0 1 1 490 162Z"/>
      <path d="M349 318L404 259A60 60 0 1 1 404 377Z"/>
      <path d="M754 318L699 259A60 60 0 1 0 699 377Z"/>
      <path d="M549 528L608 474A60 60 0 1 0 490 474Z"/>
    </g>
    <g stroke="var(--blue-mid)" stroke-width="2">
      <circle cx="549" cy="176" r="46"/><circle cx="424" cy="318" r="46"/><circle cx="679" cy="318" r="46"/><circle cx="549" cy="460" r="46"/>
    </g>
    <g stroke="var(--blue-mid)" stroke-width="1.6" stroke-linejoin="round">
      <rect x="530" y="160" width="22" height="14" rx="2"/><rect x="552" y="168" width="16" height="11" rx="2"/><circle cx="541" cy="190" r="5"/><path d="M530 202q11-10 22 0"/>
      <circle cx="424" cy="302" r="6"/><path d="M412 320q12-12 24 0"/><path d="M404 326H444M410 326V340M438 326V340"/>
      <circle cx="668" cy="306" r="5"/><circle cx="690" cy="306" r="5"/><path d="M659 326q9-12 18 0M681 326q9-12 18 0M662 330V340M696 330V340"/>
      <circle cx="549" cy="460" r="10"/><circle cx="549" cy="460" r="18" stroke-dasharray="5 4"/>
    </g>
  </svg>

  <div class="abs point left" style="left:152px;top:145px;width:250px"><h3>Nemo enim ipsam voluptate</h3><p>Lorem ipsum dolor sit amet, consectetur adipiscing elit, sed do eiusmod tempor incididunt ut labore et dolore magna aliqua.</p></div>
  <div class="abs point" style="left:694px;top:145px;width:250px"><h3>Nemo enim ipsam voluptate</h3><p>Lorem ipsum dolor sit amet, consectetur adipiscing elit, sed do eiusmod tempor incididunt ut labore et dolore magna aliqua.</p></div>
  <div class="abs point left bottom" style="left:152px;top:405px;width:250px"><p>Lorem ipsum dolor sit amet, consectetur adipiscing elit, sed do eiusmod tempor incididunt ut labore et dolore magna aliqua.</p><h3>Nemo enim ipsam voluptate</h3></div>
  <div class="abs point bottom" style="left:694px;top:405px;width:250px"><p>Lorem ipsum dolor sit amet, consectetur adipiscing elit, sed do eiusmod tempor incididunt ut labore et dolore magna aliqua.</p><h3>Nemo enim ipsam voluptate</h3></div>

  <footer class="footer"><div class="social"><span></span><span></span><span></span><span></span></div><div class="page-no">2</div></footer>
</section>

<!-- Slide 3: Feature panel -->
<section class="slide" style="top:1408px">
  <h2 class="slide-title" style="left:93px">Nemo enim ipsam voluptatem quia voluptas sit</h2>
  <div class="brand header-brand">KestrovaAI</div>
  <div class="header-rule" style="left:93px;width:911px"></div>
  <div class="photo" style="left:48px;top:107px;width:335px;height:407px;background:radial-gradient(circle at 50% 42%,#1f8fd6 0,#0b3b6a 30%,#07101f 70%)" role="img" aria-label="Illustration of a glowing digital brain above a circuit board"></div>
  <div class="abs feature-head">NEMO ENIM IPSAM VOLU</div>
  <div class="abs feature-body">
    <p>Lorem ipsum dolor sit amet, consectetur adipiscing elit, sed do eiusmod tempor incididunt ut labore et dolore magna aliqua. Ut enim ad minim veniam, quis nostrud exercitation ullamco laboris nisi ut aliquip ex ea commodo consequat. Duis aute irure dolor in reprehenderit in voluptate velit esse cillum dolore eu fugiat nulla pariatur. Excepteur sint occaecat cupidatat non proident, sunt in culpa qui officia deserunt mollit anim id est laborum. Lorem ipsum dolor sit amet, consectetur adipiscing elit, sed do eiusmod tempor incididunt ut labore et dolore magna aliqua. Ut enim ad minim veniam, quis nostrud exercitation ullamco laboris nisi ut aliquip ex ea commodo consequat. Duis aute irure dolor in reprehenderit in voluptate velit esse cillum dolore eu fugiat nulla pariatur. Excepteur sint occaecat cupidatat non proident, sunt in culpa qui officia deserunt mollit anim id est laborum.</p>
    <p>Lorem ipsum dolor sit amet, consectetur adipiscing elit, sed do eiusmod tempor incididunt ut labore et dolore magna aliqua.</p>
  </div>
  <div class="photo" style="left:718px;top:107px;width:335px;height:407px;background:radial-gradient(circle at 65% 45%,#7d8796 0,#2c3545 40%,#0c1220 80%)" role="img" aria-label="Illustration of a thoughtful humanoid robot"></div>
  <footer class="footer"><div class="social"><span></span><span></span><span></span><span></span></div><div class="page-no">3</div></footer>
</section>

<!-- Slide 4: Bar chart -->
<section class="slide" style="top:2087px">
  <h2 class="slide-title">Nemo enim ipsam voluptatem quia voluptas sit</h2>
  <div class="brand header-brand">KestrovaAI</div>
  <div class="header-rule"></div><div class="header-accent"></div>
  <p class="abs chart-intro">At vero eos et accusamus et iusto odio dignissimos ducimus qui blanditiis praesentium voluptatum deleniti atque corrupti quos dolores et quas molestias excepturi sint occaecati cupiditate non provident, similique sunt in culpa qui officia At vero eos et accusamus et iusto odio dignissimos ducimus qui blanditiis praesentium voluptatum deleniti atque corrupti quos dolores et quas molestias excepturi sint occaecati cupiditate non provident, similique sunt in culpa qui officia</p>
  <div class="abs baseline"></div>
  <svg class="abs" style="left:0;top:0" width="1096" height="430" viewBox="0 0 1096 430">
    <g>
      <path d="M85 294L122 274L159 294V400L122 420L85 400Z" fill="var(--teal)"/><path d="M85 294L122 274L159 294L122 314Z" fill="#2fa3ad"/><path d="M122 314L159 294V400L122 420Z" fill="#145e69"/>
      <path d="M296 248L333 228L370 248V400L333 420L296 400Z" fill="var(--crimson)"/><path d="M296 248L333 228L370 248L333 268Z" fill="#d2264d"/><path d="M333 268L370 248V400L333 420Z" fill="#7d0f2a"/>
      <path d="M506 203L543 183L580 203V400L543 420L506 400Z" fill="var(--olive)"/><path d="M506 203L543 183L580 203L543 223Z" fill="#c5c52b"/><path d="M543 223L580 203V400L543 420Z" fill="#7a7a14"/>
      <path d="M716 155L753 135L790 155V400L753 420L716 400Z" fill="var(--amber)"/><path d="M716 155L753 135L790 155L753 175Z" fill="#f0b445"/><path d="M753 175L790 155V400L753 420Z" fill="#c27c15"/>
      <path d="M926 139L963 119L1000 139V400L963 420L926 400Z" fill="var(--indigo)"/><path d="M926 139L963 119L1000 139L963 159Z" fill="#2a2ab0"/><path d="M963 159L1000 139V400L963 420Z" fill="#0b0b52"/>
    </g>
  </svg>
  <div class="bar-label" style="left:42px;top:449px"><i></i><h4>Duis aute irure</h4><p>At vero eos et accusamus et iu sto odio dignissimos du</p></div>
  <div class="bar-label" style="left:253px;top:449px"><i></i><h4>Duis aute irure</h4><p>At vero eos et accusamus et iu sto odio dignissimos du</p></div>
  <div class="bar-label" style="left:463px;top:449px"><i></i><h4>Duis aute irure</h4><p>At vero eos et accusamus et iu sto odio dignissimos du</p></div>
  <div class="bar-label" style="left:673px;top:449px"><i></i><h4>Duis aute irure</h4><p>At vero eos et accusamus et iu sto odio dignissimos du</p></div>
  <div class="bar-label" style="left:883px;top:449px"><i></i><h4>Duis aute irure</h4><p>At vero eos et accusamus et iu sto odio dignissimos du</p></div>
  <footer class="footer"><div class="social"><span></span><span></span><span></span><span></span></div><div class="page-no">4</div></footer>
</section>

<!-- Slide 5: Story with images -->
<section class="slide" style="top:2767px">
  <h2 class="slide-title">Nemo enim ipsam voluptatem quia voluptas sit</h2>
  <div class="brand header-brand">KestrovaAI</div>
  <div class="header-rule"></div><div class="header-accent"></div>
  <p class="abs story">Lorem ipsum dolor sit amet, consectetur adipiscing elit, sed do eiusmod tempor incididunt ut labore et dolore magna aliqua. Ut enim ad minim veniam, quis nostrud exercitation ullamco laboris nisi ut aliquip ex ea commodo consequat. Duis aute irure dolor in reprehenderit in voluptate velit esse cillum dolore eu fugiat nulla pariatur. Excepteur sint occaecat cupidatat non proident, sunt in culpa qui officia deserunt mollit anim id est laborum. Sed ut perspiciatis unde omnis iste natus error sit voluptatem accusantium doloremque laudantium, totam rem aperiam, eaque ipsa quae ab illo inventore veritatis et quasi architecto beatae vitae dicta sunt explicabo. Nemo enim ipsam voluptatem quia voluptas sit aspernatur aut odit aut fugit, sed quia consequuntur magni dolores eos qui ratione voluptatem sequi nesciunt. Neque porro quisquam est, qui dolorem ipsum quia dolor sit amet, consectetur, adipisci velit, sed quia non numquam eius modi tempora incidunt ut labore et dolore magnam aliquam quaerat voluptatem. Ut enim ad minima veniam</p>
  <div class="photo" style="left:48px;top:260px;width:710px;height:278px;background:radial-gradient(circle at 50% 50%,#6fc9f0 0,#1a5c93 28%,#0a1a33 70%)" role="img" aria-label="Illustration of a robotic hand and a human hand reaching toward glowing AI letters"></div>
  <div class="photo framed" style="left:695px;top:88px;width:360px;height:363px;background:radial-gradient(circle at 40% 38%,#e58a3a 0,#6a3a34 25%,#14263f 60%,#0b1526 100%)" role="img" aria-label="Illustration of a hand touching a glowing AI chip surrounded by network icons"></div>
  <footer class="footer"><div class="social"><span></span><span></span><span></span><span></span></div><div class="page-no">5</div></footer>
</section>

<!-- Slide 6: Thank you -->
<section class="slide closing" style="top:3444px">
  <div class="abs brand closing-brand" style="color:var(--white)">KestrovaAI</div>
  <div class="abs thanks">THANK YOU</div>
  <div class="contact" style="left:191px">
    <div class="icon"><svg width="22" height="22" viewBox="0 0 24 24" fill="#fff"><path d="M12 2a7 7 0 0 0-7 7c0 5 7 13 7 13s7-8 7-13a7 7 0 0 0-7-7zm0 9.5A2.5 2.5 0 1 1 12 6.5a2.5 2.5 0 0 1 0 5z"/></svg></div>
    <h5>ADDRESS:</h5><p>123,Lorem ipsum dolor sit<br>amet, consectetur</p>
  </div>
  <div class="contact" style="left:426px">
    <div class="icon"><svg width="22" height="22" viewBox="0 0 24 24" fill="#fff"><path d="M6.6 10.8a15 15 0 0 0 6.6 6.6l2.2-2.2a1 1 0 0 1 1-.25 11.4 11.4 0 0 0 3.6.6 1 1 0 0 1 1 1V20a1 1 0 0 1-1 1A17 17 0 0 1 3 4a1 1 0 0 1 1-1h3.5a1 1 0 0 1 1 1c0 1.25.2 2.45.6 3.6a1 1 0 0 1-.25 1z"/></svg></div>
    <h5>PHONE:</h5><p>+1 888 888 8888</p>
  </div>
  <div class="contact" style="left:663px">
    <div class="icon"><svg width="22" height="22" viewBox="0 0 24 24" fill="#fff"><path d="M3 5h18v14H3z" opacity="0"/><path d="M3 6h18v12H3zM3 6l9 7 9-7" fill="none" stroke="#fff" stroke-width="2" stroke-linejoin="round"/></svg></div>
    <h5>EMAIL ADDRESS:</h5><p>info@companyname.com</p>
  </div>
  <footer class="footer"><div class="social"><span></span><span></span><span></span><span></span></div><div class="page-no">6</div></footer>
</section>

</body>
</html>
```